Website for Excavator and Earthworks Company

We require a modern, sleek and practical website for our newly created earthworks/excavator business in Perth, Western Australia called Bluegum Ridge Earthworks.

The website should have a modern, cutting edge feel but only needs to be relatively simplistic in it's layout and eventual functionality.

Some pages it should have would be Home, About, Projects and Contact Us.

```html
<!DOCTYPE html>
<html lang="en">
<head>
<meta charset="utf-8">
<title>Bluegum Ridge Earthworks</title>
<link rel="stylesheet" href="https://fonts.googleapis.com/css2?family=Montserrat:wght@500;600;700;800&family=Inter:wght@400;500;600&display=swap">
<style>
:root{
  --green:#bfd600;
  --green-soft:#f4f9cf;
  --green-tag:#eef6b8;
  --ink:#111111;
  --text:#2a2a2a;
  --grey:#f2f1f3;
  --field:#efeff1;
  --black:#000000;
  --white:#ffffff;
}
*{margin:0;padding:0;box-sizing:border-box}
html,body{width:1200px;height:3894px;overflow:hidden}
body{position:relative;background:var(--white);font-family:"Inter",sans-serif;color:var(--text)}
.abs{position:absolute}
.head{font-family:"Montserrat",sans-serif;font-weight:800;color:var(--ink);text-transform:uppercase;letter-spacing:.2px}
.tag{position:absolute;height:27px;padding:0 16px;background:var(--green-tag);font-family:"Montserrat",sans-serif;font-weight:600;font-size:15px;line-height:27px;color:var(--ink);clip-path:polygon(4% 0,100% 0,96% 100%,0 100%)}
.rule{position:absolute;width:46px;height:2px;background:var(--ink)}
.btn{position:absolute;background:var(--green);color:var(--ink);font-family:"Montserrat",sans-serif;font-weight:700;font-size:14px;text-transform:uppercase;display:flex;align-items:center;justify-content:center;gap:12px;clip-path:polygon(6% 0,100% 0,94% 100%,0 100%)}
.photo{position:absolute}

/* header */
.site-header{position:absolute;left:0;top:0;width:1200px;height:94px;background:var(--white)}
.brand{position:absolute;left:151px;top:28px;display:flex;align-items:center;gap:12px}
.brand-mark{width:36px;height:36px;background:var(--green)}
.brand-name{font-family:"Montserrat",sans-serif;font-weight:800;font-size:19px;line-height:20px;color:var(--ink);text-transform:uppercase}
.nav{position:absolute;top:38px;left:491px;display:flex;gap:31px;font-family:"Montserrat",sans-serif;font-weight:600;font-size:13px;color:var(--ink)}
.nav .active{color:var(--green);position:relative}
.nav .active::before{content:"";position:absolute;left:0;right:0;top:-8px;height:2px;background:var(--green)}
.nav .active::after{content:"";position:absolute;left:0;right:0;bottom:-9px;height:2px;background:var(--green)}
.call-box{position:absolute;left:848px;top:0;width:352px;height:94px;background:var(--green);clip-path:polygon(0 0,100% 0,100% 100%,8% 100%)}
.call-box svg{position:absolute;left:46px;top:31px}
.call-label{position:absolute;left:78px;top:27px;font-family:"Montserrat",sans-serif;font-weight:500;font-size:12px;color:var(--ink)}
.call-num{position:absolute;left:76px;top:43px;font-family:"Montserrat",sans-serif;font-weight:700;font-size:18px;color:var(--ink)}

/* hero */
.hero{position:absolute;left:0;top:94px;width:1200px;height:551px;background:linear-gradient(100deg,#5c3a22 0%,#7a4a2a 35%,#8d5a34 55%,#6f6a55 75%,#b9b8b2 100%)}
.hero-shade{position:absolute;inset:0;background:linear-gradient(90deg,rgba(0,0,0,.35),rgba(0,0,0,0) 60%)}
.hero h1{position:absolute;left:148px;top:108px;font-family:"Montserrat",sans-serif;font-weight:800;font-size:40px;line-height:57px;color:var(--white);text-transform:uppercase}
.hero h1 span{color:var(--green)}
.hero p{position:absolute;left:154px;top:290px;font-size:21px;line-height:30px;color:var(--white)}
.dots{position:absolute;top:508px;left:562px;display:flex;gap:13px}
.dots i{width:8px;height:8px;border-radius:50%;background:var(--white)}
.dots i.on{background:var(--green)}

/* services */
.acc-open{position:absolute;left:609px;top:690px;width:440px;height:192px;background:var(--green-soft);clip-path:polygon(0 0,100% 0,100% 100%,4% 100%)}
.acc-open .photo{right:0;top:0;width:166px;height:192px;background:linear-gradient(160deg,#d89a3a,#8b6a3b 50%,#5a4733);clip-path:polygon(12% 0,100% 0,100% 100%,0 100%)}
.acc-title{position:absolute;left:50px;top:14px;font-size:15px;color:var(--ink);display:flex;gap:14px;align-items:center}
.acc-body{position:absolute;left:38px;top:62px;width:214px;font-size:10.5px;line-height:14px;color:#333}
.acc-more{position:absolute;left:42px;top:148px;height:22px;padding:0 14px;background:var(--green);font-family:"Montserrat",sans-serif;font-weight:700;font-size:10px;line-height:22px;color:var(--ink);clip-path:polygon(6% 0,100% 0,94% 100%,0 100%)}
.acc-item{position:absolute;left:632px;width:417px;height:42px;border:1.5px solid #444;display:flex;align-items:center;gap:14px;padding-left:18px;font-size:14.5px;color:var(--ink);clip-path:polygon(0 0,100% 0,100% 100%,1% 100%)}

/* about */
.about-text p{font-size:12.5px;line-height:18px;color:#333;margin-bottom:17px}
.list li{list-style:none;display:flex;align-items:center;gap:16px;font-size:15.5px;color:#222;height:27px}

/* contact form */
.field{position:absolute;left:626px;width:338px;background:var(--field);font-size:12.5px;color:#333;padding:12px 0 0 26px;clip-path:polygon(0 0,100% 0,100% 100%,1.5% 100%)}
.submit{position:absolute;left:659px;top:3338px;width:338px;height:50px;background:var(--green);font-family:"Montserrat",sans-serif;font-weight:700;font-size:20px;color:var(--ink);display:flex;align-items:center;justify-content:center;clip-path:polygon(3% 0,100% 0,97% 100%,0 100%)}

/* footer */
.site-footer{position:absolute;left:0;top:3490px;width:1200px;height:404px;background:var(--black);color:var(--white)}
.foot-brand{position:absolute;left:151px;top:72px;display:flex;align-items:center;gap:14px}
.foot-brand .brand-mark{width:48px;height:48px}
.foot-brand .brand-name{color:var(--green);font-size:20px;line-height:25px}
.foot-head{position:absolute;left:453px;top:48px;font-family:"Montserrat",sans-serif;font-weight:700;font-size:15px}
.foot-item{position:absolute;left:452px;display:flex;gap:14px;font-family:"Montserrat",sans-serif;font-weight:500;font-size:12.5px;line-height:24px;text-transform:uppercase}
.foot-item svg{flex:none;margin-top:5px}
.foot-line{position:absolute;left:151px;width:514px;height:1px;background:#333}
.foot-nav{position:absolute;left:250px;top:259px;font-family:"Montserrat",sans-serif;font-weight:500;font-size:12.5px;word-spacing:2px}
.copy{position:absolute;left:0;width:816px;top:339px;text-align:center;font-size:12.5px}
</style>
</head>
<body>

<header class="site-header">
  <div class="brand"><div class="brand-mark"></div><div class="brand-name">Bluegum Ridge<br>Earthworks</div></div>
  <nav class="nav"><span class="active">HOME</span><span>ABOUT</span><span>PROJECTS</span><span>CONTACT US</span></nav>
  <div class="call-box">
    <svg width="26" height="26" viewBox="0 0 24 24"><path fill="#111" d="M6.6 10.8a15.1 15.1 0 0 0 6.6 6.6l2.2-2.2a1 1 0 0 1 1-.25 11.4 11.4 0 0 0 3.6.57 1 1 0 0 1 1 1V20a1 1 0 0 1-1 1A17 17 0 0 1 3 4a1 1 0 0 1 1-1h3.5a1 1 0 0 1 1 1c0 1.25.2 2.45.57 3.6a1 1 0 0 1-.25 1z"/></svg>
    <div class="call-label">CALL US</div>
    <div class="call-num">+61 8 5550 1427</div>
  </div>
</header>

<section class="hero" role="img" aria-label="Excavator digging a trench through red soil in a forest clearing">
  <div class="hero-shade"></div>
  <h1>Precision earthmoving.<br>Solid foundations.<br><span>Built to rise.</span></h1>
  <p>Reliable excavation and earthworks services<br>across Perth and Western Australia.</p>
  <div class="btn" style="left:159px;top:382px;width:224px;height:45px">View our projects
    <svg width="10" height="14" viewBox="0 0 10 14"><path d="M2 1l6 6-6 6" fill="none" stroke="#111" stroke-width="2"/></svg></div>
  <div class="dots"><i class="on"></i><i></i><i></i><i></i></div>
</section>

<!-- services -->
<div class="tag" style="left:151px;top:696px">OUR SERVICES</div>
<h2 class="head abs" style="left:151px;top:742px;font-size:25px;line-height:35px">Professional<br>earthmoving solutions</h2>
<div class="rule" style="left:151px;top:831px"></div>
<div class="photo" role="img" aria-label="Wheel loader on a gravel pile" style="left:151px;top:879px;width:230px;height:292px;background:linear-gradient(170deg,#9a9a98,#c4c3c0 60%,#e2e0dc);clip-path:polygon(0 0,100% 0,100% 100%,3% 100%)"></div>
<div class="photo" role="img" aria-label="Excavator working on brown earth from above" style="left:355px;top:879px;width:240px;height:292px;background:linear-gradient(160deg,#8b5a35,#b07a4c 50%,#c79566);clip-path:polygon(0 0,100% 0,100% 100%,11% 100%)"></div>

<div class="acc-open">
  <div class="acc-title"><svg width="12" height="8" viewBox="0 0 12 8"><path d="M1 7l5-5 5 5" fill="none" stroke="#111" stroke-width="1.8"/></svg>Earthmoving &amp; Excavation</div>
  <div class="acc-body">Lorem ipsum dolor sit amet, cons ectetur adipiscing elit, sed do eiusmod tempor incididunt ut labore et dolore magna aliqua. Ut enim ad minim veniam, quis nostrud exercitation ullamco laboris nisi.</div>
  <div class="acc-more">READ MORE ›</div>
  <div class="photo" role="img" aria-label="Yellow excavator on a dig site"></div>
</div>
<div class="acc-item" style="top:902px"><svg width="12" height="8" viewBox="0 0 12 8"><path d="M1 1l5 5 5-5" fill="none" stroke="#111" stroke-width="1.8"/></svg>Drilling and Trenching</div>
<div class="acc-item" style="top:958px"><svg width="12" height="8" viewBox="0 0 12 8"><path d="M1 1l5 5 5-5" fill="none" stroke="#111" stroke-width="1.8"/></svg>Backfilling &amp; Compaction</div>
<div class="acc-item" style="top:1015px"><svg width="12" height="8" viewBox="0 0 12 8"><path d="M1 1l5 5 5-5" fill="none" stroke="#111" stroke-width="1.8"/></svg>Concrete &amp; Rock Removal</div>
<div class="acc-item" style="top:1071px"><svg width="12" height="8" viewBox="0 0 12 8"><path d="M1 1l5 5 5-5" fill="none" stroke="#111" stroke-width="1.8"/></svg>Skid Steel Services</div>
<div class="acc-item" style="top:1127px"><svg width="12" height="8" viewBox="0 0 12 8"><path d="M1 1l5 5 5-5" fill="none" stroke="#111" stroke-width="1.8"/></svg>Tree Stump Grinding</div>

<!-- about -->
<div class="abs" style="left:0;top:1225px;width:1200px;height:495px;background:var(--green);clip-path:polygon(0 0,10px 0,100px 100%,0 100%)"></div>
<div class="abs" style="left:0;top:1225px;width:720px;height:495px;background:var(--grey);clip-path:polygon(10px 0,100% 0,100% 100%,100px 100%)"></div>
<div class="abs" style="left:580px;top:1225px;width:620px;height:495px;background:var(--green);clip-path:polygon(0 0,100% 0,100% 100%,17% 100%)"></div>
<div class="photo" role="img" aria-label="Orange excavator on a gravel road among tall pine trees" style="left:604px;top:1225px;width:596px;height:495px;background:linear-gradient(180deg,#7fa8d8 0%,#4f7a4a 40%,#3e5b34 60%,#a39a86 85%,#c9c3b4 100%);clip-path:polygon(0 0,81% 0,100% 100%,15% 100%)"></div>
<div class="tag" style="left:151px;top:1261px">ABOUT US</div>
<h2 class="head abs" style="left:151px;top:1302px;font-size:25px;line-height:35px">Raising the groundwork<br>for what comes next</h2>
<div class="rule" style="left:151px;top:1384px"></div>
<div class="about-text abs" style="left:151px;top:1414px;width:420px">
  <p>Bluegum Ridge Earthworks is a locally owned Perth-based earthmoving company delivering dependable excavation solutions for residential, commercial and civil projects.</p>
  <p>Built on precision, safety and efficiency, we combine modern machinery with experienced operators to ensure every job is completed to the highest standard — on time and on budget.</p>
  <p>Whether it's a small residential dig or a large-scale earthworks project, we approach every site with the same commitment to quality.</p>
</div>
<div class="btn" style="left:156px;top:1618px;width:196px;height:46px">Call to book</div>

<!-- plant hire -->
<div class="abs" style="left:0;top:1720px;width:480px;height:627px;background:var(--green-soft);clip-path:polygon(0 0,100% 0,99% 4%,6% 4%,25% 100%,0 100%)"></div>
<div class="photo" role="img" aria-label="Orange excavator on a dark earth mound against a blue sky" style="left:53px;top:1765px;width:500px;height:548px;background:linear-gradient(180deg,#5e8fe0 0%,#8fb4ea 55%,#2c2824 72%,#141210 100%);clip-path:polygon(0 0,80% 0,100% 100%,17% 100%)"></div>
<h2 class="head abs" style="left:610px;top:1776px;font-size:25px;line-height:35px">We have the quality plant<br>hire and skilled operators<br>to complete your project<br>across Perth.</h2>
<div class="rule" style="left:610px;top:1937px"></div>
<p class="abs" style="left:610px;top:1971px;width:450px;font-size:12px;line-height:18px;color:#333">Sed ut perspiciatis unde omnis iste natus error sit voluptatem accusantium doloremque laudantium, totam rem aperiam, eaque ipsa quae ab illo inventore veritatis et quasi architecto beatae vitae dicta sunt explicabo.</p>
<ul class="list abs" style="left:614px;top:2048px">
  <li><svg width="8" height="12" viewBox="0 0 8 12"><path d="M1 1l5 5-5 5" fill="none" stroke="#bfd600" stroke-width="1.6"/></svg>Excavator Hire Perth</li>
  <li><svg width="8" height="12" viewBox="0 0 8 12"><path d="M1 1l5 5-5 5" fill="none" stroke="#bfd600" stroke-width="1.6"/></svg>Skid Steer Hire Perth</li>
  <li><svg width="8" height="12" viewBox="0 0 8 12"><path d="M1 1l5 5-5 5" fill="none" stroke="#bfd600" stroke-width="1.6"/></svg>Track Loader Hire Perth</li>
  <li><svg width="8" height="12" viewBox="0 0 8 12"><path d="M1 1l5 5-5 5" fill="none" stroke="#bfd600" stroke-width="1.6"/></svg>Water Cart Hire Perth</li>
  <li><svg width="8" height="12" viewBox="0 0 8 12"><path d="M1 1l5 5-5 5" fill="none" stroke="#bfd600" stroke-width="1.6"/></svg>Grader Hire Perth</li>
  <li><svg width="8" height="12" viewBox="0 0 8 12"><path d="M1 1l5 5-5 5" fill="none" stroke="#bfd600" stroke-width="1.6"/></svg>Road Truck Hire</li>
</ul>
<div class="btn" style="left:619px;top:2239px;width:195px;height:46px">Get a free quote</div>

<!-- projects -->
<section class="abs" style="left:0;top:2347px;width:1200px;height:619px;background:var(--green-soft)">
  <div class="tag" style="left:499px;top:50px">FEATURED PROJECTS</div>
  <h2 class="head abs" style="left:0;width:1200px;text-align:center;top:94px;font-size:25px">Our work speaks for itself</h2>
  <div class="rule" style="left:577px;top:149px"></div>
  <svg class="abs" style="left:0;top:192px" width="1200" height="327" viewBox="0 0 1200 327">
    <g role="img" aria-label="Orange excavator bucket in soil"><polygon points="0,0 193,0 219,327 0,327" fill="#9a5a3a"/></g>
    <g role="img" aria-label="Bulldozer blade pushing dirt"><polygon points="197,0 452,0 489,327 224,327" fill="#b0794d"/></g>
    <g role="img" aria-label="Yellow wheel loader at a quarry"><polygon points="462,0 722,0 753,327 494,327" fill="#8d8a80"/></g>
    <g role="img" aria-label="Green backhoe loader among trees"><polygon points="732,0 990,0 1022,327 762,327" fill="#5f6a4c"/></g>
    <g role="img" aria-label="Excavator on brown earth from above"><polygon points="1000,0 1200,0 1200,327 1032,327" fill="#a8714a"/></g>
  </svg>
  <svg class="abs" style="left:532px;top:554px" width="136" height="16" viewBox="0 0 136 16">
    <path d="M7 2l-5 6 5 6" fill="none" stroke="#333" stroke-width="1.5"/>
    <circle cx="30" cy="8" r="4.5" fill="#bfd600"/><circle cx="50" cy="8" r="4.5" fill="#dfe89a"/><circle cx="70" cy="8" r="4.5" fill="#dfe89a"/><circle cx="90" cy="8" r="4.5" fill="#dfe89a"/><circle cx="110" cy="8" r="4.5" fill="#dfe89a"/>
    <path d="M129 2l5 6-5 6" fill="none" stroke="#333" stroke-width="1.5"/>
  </svg>
</section>

<!-- contact -->
<div class="tag" style="left:156px;top:3057px">CONTACT US</div>
<h2 class="head abs" style="left:156px;top:3102px;font-size:29px;line-height:43px">Ready to get your<br>project moving?</h2>
<div class="rule" style="left:156px;top:3208px"></div>
<p class="abs" style="left:156px;top:3244px;width:400px;font-size:16px;line-height:26px;color:#333">Whether you're preparing a site, planning a build or need reliable excavation services — Bluegum Ridge Earthworks is ready to help.</p>
<div class="btn" style="left:156px;top:3353px;width:156px;height:46px">Get a quote</div>

<svg class="abs" style="left:570px;top:3015px" width="474" height="422" viewBox="0 0 474 422">
  <polygon points="4,4 438,4 470,418 36,418" fill="none" stroke="#eef6b8" stroke-width="5"/>
</svg>
<div class="field" style="top:3054px;height:37px">Full Name</div>
<div class="field" style="top:3104px;height:37px">Email id</div>
<div class="field" style="top:3154px;height:37px">Phone</div>
<div class="field" style="top:3203px;height:121px;width:355px">Message</div>
<div class="submit">SUBMIT</div>

<footer class="site-footer">
  <div class="foot-brand"><div class="brand-mark"></div><div class="brand-name">Bluegum Ridge<br>Earthworks</div></div>
  <div class="foot-head">CONTACT US</div>
  <div class="foot-item" style="top:80px">
    <svg width="12" height="16" viewBox="0 0 12 16"><path d="M6 0a6 6 0 0 0-6 6c0 4.5 6 10 6 10s6-5.5 6-10a6 6 0 0 0-6-6zm0 8.3A2.3 2.3 0 1 1 6 3.7a2.3 2.3 0 0 1 0 4.6z" fill="#fff"/></svg>
    <span>418 Wattle Crest Road, Unit 12,<br>Perth, Western Australia</span></div>
  <div class="foot-item" style="top:141px">
    <svg width="14" height="14" viewBox="0 0 24 24"><path fill="#fff" d="M6.6 10.8a15.1 15.1 0 0 0 6.6 6.6l2.2-2.2a1 1 0 0 1 1-.25 11.4 11.4 0 0 0 3.6.57 1 1 0 0 1 1 1V20a1 1 0 0 1-1 1A17 17 0 0 1 3 4a1 1 0 0 1 1-1h3.5a1 1 0 0 1 1 1c0 1.25.2 2.45.57 3.6a1 1 0 0 1-.25 1z"/></svg>
    <span>+61 8 5550 1427</span></div>
  <div class="foot-item" style="top:176px">
    <svg width="14" height="11" viewBox="0 0 14 11"><path d="M0 0h14v11H0z" fill="#fff"/><path d="M0 0l7 6 7-6" fill="none" stroke="#000" stroke-width="1.2"/></svg>
    <span>info@bluegumridge.com</span></div>
  <div class="photo" role="img" aria-label="Street map of central Perth showing the business location" style="left:725px;top:41px;width:324px;height:330px;background:linear-gradient(135deg,#e9eef3,#d6e6d2 55%,#a9cdee)"></div>
  <div class="foot-line" style="top:238px"></div>
  <div class="foot-nav">HOME &nbsp;\&nbsp; ABOUT &nbsp;\&nbsp; PROJECTS &nbsp;\&nbsp; CONTACT US</div>
  <div class="foot-line" style="top:301px"></div>
  <div class="copy">Copyright © 2026 All Rights Reserved</div>
</footer>

</body>
</html>
```